Business Card Design needed - Something Awesome!

Need a business card designed. Company is "Marlowe Advisory" we do consulting and also have sales automation technology.
I'm going to use thick stock or metal, something really nice... I was thinking about a QR Code on the back that would just upload my contact info to the persons contact, etc -

This is a Strategy Company with a tech feel. I'm open to ideas but really want this to be nice!

I need a template that should include:

Name | Position or Title
D: 415.902.3376
www.marloweadvisory.example

I'm going to attach my contact so you can use that one, I need to get this printed.

Target Market(s)

Small to mid size customers, Entrepreneurs etc.

Industry/Entity Type

Consulting, Tech, Private Equity.

Contact Information for Business Card

Name, Phone, Maybe email, URL

Font styles to use
Sans Serif

Colors

Designer to choose only greyscale colors for use in the design.

Requirements
Must have
• Fresh, Clean, stand out from the crowd - will be on thick stock or metal.
Nice to have
• Clean, simple yet impactful.
Should not have
• Not cartoonish

```html
<!DOCTYPE html>
<html lang="en">
<head>
<meta charset="utf-8">
<title>Marlowe Advisory – Business Card</title>
<link href="https://fonts.googleapis.com/css2?family=Lato:wght@400;700&display=swap" rel="stylesheet">
<style>
  :root {
    --backdrop: #262626;
    --card: #1c1c1c;
    --card-edge: #2e2e2e;
    --foil: #b8b8b8;
    --foil-soft: #9a9a9a;
  }
  html, body {
    margin: 0;
    width: 1200px;
    height: 958px;
    overflow: hidden;
    background: var(--backdrop);
    font-family: "Lato", sans-serif;
  }
  .sheet {
    width: 1200px;
    height: 958px;
    display: flex;
    align-items: center;
    justify-content: center;
    gap: 90px;
  }
  .card {
    position: relative;
    width: 330px;
    height: 578px;
    background: var(--card);
    border-radius: 3px;
    box-shadow: 0 0 0 1px var(--card-edge), 0 18px 40px rgba(0,0,0,.45);
    color: var(--foil);
    overflow: hidden;
  }
  .card-front .wordmark {
    position: absolute;
    left: 50%;
    top: 50%;
    transform: translate(-50%, -50%) rotate(-90deg);
    white-space: nowrap;
    display: flex;
    align-items: center;
    gap: 14px;
    font-weight: 400;
    font-size: 36px;
    letter-spacing: 3px;
    text-transform: uppercase;
  }
  .wordmark .mark-square {
    width: 20px;
    height: 20px;
    background: var(--foil);
  }
  .card-back .details {
    position: absolute;
    left: 0;
    right: 0;
    top: 318px;
    text-align: center;
  }
  .brand-line {
    display: flex;
    align-items: center;
    justify-content: center;
    gap: 8px;
    font-size: 15px;
    letter-spacing: 2px;
    text-transform: uppercase;
    margin-bottom: 22px;
  }
  .brand-line .mark-square {
    width: 12px;
    height: 12px;
    background: var(--foil);
  }
  .person-name {
    font-weight: 700;
    font-size: 23px;
    margin: 0;
  }
  .person-title {
    font-size: 15px;
    color: var(--foil-soft);
    margin: 4px 0 10px;
  }
  .divider {
    width: 34px;
    height: 1px;
    background: var(--foil-soft);
    margin: 0 auto 10px;
  }
  .contact-list {
    list-style: none;
    margin: 0;
    padding: 0;
    font-size: 15px;
    line-height: 1.5;
    color: var(--foil-soft);
  }
</style>
</head>
<body>
  <main class="sheet">
    <section class="card card-front" aria-label="Card front">
      <div class="wordmark">
        <span class="mark-square"></span>
        <span>Marlowe Advisory</span>
      </div>
    </section>

    <section class="card card-back" aria-label="Card back">
      <div class="details">
        <div class="brand-line">
          <span class="mark-square"></span>
          <span>Marlowe Advisory</span>
        </div>
        <h1 class="person-name">Adrian K. Vollmer</h1>
        <p class="person-title">Founder/CEO</p>
        <div class="divider"></div>
        <ul class="contact-list">
          <li>415.902.3376</li>
          <li>hello@marloweadvisory.example</li>
          <li>marloweadvisory.example</li>
        </ul>
      </div>
    </section>
  </main>
</body>
</html>
```